QVR business card

Need a business card for a company that provides instructional design and elearning development services. The website is here: http://quorvane.studio/

I'm attaching a current logo, as well as the old business card design. While I like to keep it clean, the old design is too simplistic for my liking. The only idea I want to reuse from the old design is placing industry jargon on the back of the card, just need a better way to present it. But if you have other ideas for the back--feel free to experiment.

Please use the colors complementary to the color we have on the website. Thank you!

```html
<!DOCTYPE html>
<html lang="en">
<head>
<meta charset="utf-8">
<title>QVR business card</title>
<link rel="stylesheet" href="https://fonts.googleapis.com/css2?family=Fira+Sans+Condensed:wght@300;400;800&family=Open+Sans:wght@400;600;700&display=swap">
<style>
  :root {
    --teal: #1db2ae;
    --teal-deep: #14a19d;
    --sand: #d8cb8a;
    --ink: #2b2b2b;
    --paper: #ffffff;
    --stage: #e9e6e1;
  }
  * { box-sizing: border-box; margin: 0; padding: 0; }
  html, body { width: 1200px; height: 935px; overflow: hidden; }
  body {
    background: var(--stage);
    font-family: "Open Sans", Arial, sans-serif;
    position: relative;
  }
  .card {
    position: absolute;
    top: 312px;
    width: 540px;
    height: 310px;
    border-radius: 4px;
    overflow: hidden;
    box-shadow: 0 8px 24px rgba(0,0,0,.15);
  }
  .card--front { left: 45px; background: var(--paper); }
  .card--back { left: 615px; background: var(--teal); }

  .card__shapes { position: absolute; inset: 0; }

  .brand {
    position: absolute;
    left: 40px; top: 122px;
    display: flex; align-items: center; gap: 12px;
  }
  .brand__mark { width: 26px; height: 26px; background: var(--teal); }
  .brand__name {
    font-weight: 700; font-size: 44px; letter-spacing: 2px;
    color: var(--sand); line-height: 1;
  }

  .contact { position: absolute; left: 340px; top: 40px; color: var(--ink); }
  .contact__name {
    font-weight: 700; font-size: 15px; letter-spacing: .5px;
    color: var(--sand); text-transform: uppercase;
  }
  .contact__role { font-size: 12px; margin-bottom: 12px; }
  .contact__list { list-style: none; font-size: 11.5px; line-height: 19px; }
  .contact__item { display: flex; align-items: center; gap: 7px; }
  .contact__icon { width: 13px; height: 13px; flex: none; }

  .pitch {
    position: absolute; left: 36px; top: 30px;
    font-family: "Fira Sans Condensed", "Arial Narrow", sans-serif;
    font-weight: 800; color: var(--paper);
    font-size: 56px; line-height: 54px; text-transform: uppercase;
  }
  .pitch__divider {
    position: absolute; left: 214px; top: 36px;
    width: 1.5px; height: 238px; background: rgba(255,255,255,.8);
  }
  .services {
    position: absolute; left: 232px; top: 34px; list-style: none;
    font-family: "Fira Sans Condensed", "Arial Narrow", sans-serif;
    font-weight: 300; color: var(--paper);
    font-size: 27px; line-height: 40px; text-transform: uppercase;
    white-space: nowrap;
  }
</style>
</head>
<body>

<section class="card card--front" aria-label="Business card front">
  <svg class="card__shapes" width="540" height="310" viewBox="0 0 540 310" aria-hidden="true">
    <path fill="var(--teal)" d="M250 0 H540 V310 H322 V186 Q322 170 306 170 H266 Q250 170 250 154 Z"/>
    <rect x="0" y="160" width="6" height="120" fill="var(--teal)"/>
    <rect x="534" y="30" width="6" height="120" fill="var(--sand)"/>
  </svg>

  <div class="brand">
    <span class="brand__mark"></span>
    <span class="brand__name">QVR</span>
  </div>

  <div class="contact">
    <p class="contact__name">Daria Venholt</p>
    <p class="contact__role">Managing Director</p>
    <ul class="contact__list">
      <li class="contact__item">
        <svg class="contact__icon" viewBox="0 0 14 14" aria-hidden="true"><rect width="14" height="14" rx="2" fill="var(--sand)"/><path d="M4 3.5 l2 .3 .4 2 -1 .8 q1 2 3 3 l.8-1 2 .4 .3 2 q-5 .5 -7.5-7.5z" fill="var(--teal)"/></svg>
        555-014-2273
      </li>
      <li class="contact__item">
        <svg class="contact__icon" viewBox="0 0 14 14" aria-hidden="true"><rect width="14" height="14" rx="2" fill="var(--sand)"/><rect x="3" y="4" width="8" height="6" fill="none" stroke="var(--teal)" stroke-width="1.2"/><path d="M3 4 l4 3.5 4-3.5" fill="none" stroke="var(--teal)" stroke-width="1.2"/></svg>
        dvenholt@quorvane.studio
      </li>
      <li class="contact__item">
        <svg class="contact__icon" viewBox="0 0 14 14" aria-hidden="true"><rect width="14" height="14" rx="2" fill="var(--sand)"/><circle cx="7" cy="7" r="4" fill="none" stroke="var(--teal)" stroke-width="1.2"/><path d="M3 7 h8 M7 3 q-2.5 4 0 8 q2.5-4 0-8" fill="none" stroke="var(--teal)" stroke-width="1"/></svg>
        www.quorvane.studio
      </li>
    </ul>
  </div>
</section>

<section class="card card--back" aria-label="Business card back">
  <h2 class="pitch">How<br>can<br>we<br>help?</h2>
  <span class="pitch__divider"></span>
  <ul class="services">
    <li>Mobile learning SCORM</li>
    <li>Instructional design LMS</li>
    <li>MOOCs eLearning HTML5</li>
    <li>Adult learning theory</li>
    <li>Gamification classroom</li>
    <li>xAPI blended learning</li>
  </ul>
</section>

</body>
</html>
```